A clean crisp business card for a Landscape Construction company. Designed to be easy to read contact/ info and also be appealing/interesting, unlike a traditional business card.

Industry/Entity Type

Landscape Construction

Contact Information for Business Card

Company name : Brambleford Landscape Construction, phone number: (877) 62Vista, website:Bramblefordyards.example, Email, sales@bramblefordyards.example

Requirements
Nice to have
• Luxurious finishes/ details…. Icons or emblems next to contact info
Should not have
• Clipart or general pictures

```html
<!DOCTYPE html>
<html lang="en">
<head>
<meta charset="utf-8">
<title>Brambleford Landscape Construction — Business Card</title>
<link rel="stylesheet" href="https://fonts.googleapis.com/css2?family=Cinzel:wght@600;700&family=Cormorant+Garamond:wght@500&display=swap">
<style>
  :root {
    --leaf: #9ccb3b;
    --sky: #1f6db5;
    --paper: #ffffff;
    --edge: #1a1a1a;
  }
  * { margin: 0; padding: 0; box-sizing: border-box; }
  html, body {
    width: 1200px;
    height: 728px;
    overflow: hidden;
    background: var(--paper);
  }
  .card {
    position: relative;
    width: 1200px;
    height: 728px;
    background: var(--paper);
    border: 1px solid var(--edge);
  }
  .brand-area {
    position: absolute;
    left: 0; top: 0;
    width: 100%;
    height: 474px;
    display: flex;
    align-items: center;
    justify-content: center;
  }
  .brand {
    display: flex;
    align-items: center;
    gap: 24px;
  }
  .brand-dot {
    width: 60px;
    height: 60px;
    border-radius: 50%;
    background: var(--leaf);
    flex: none;
  }
  .brand-name {
    font-family: "Cinzel", serif;
    font-weight: 600;
    color: var(--sky);
    text-align: center;
    line-height: 1;
  }
  .brand-name .primary {
    display: block;
    font-size: 64px;
    letter-spacing: 1px;
  }
  .brand-name .secondary {
    display: block;
    margin-top: 14px;
    font-size: 22px;
    letter-spacing: 6px;
  }
  .company-panel {
    position: absolute;
    left: 0; top: 474px;
    width: 508px;
    height: 254px;
    background: var(--leaf);
    padding: 52px 0 0 71px;
  }
  .company-name {
    font-family: "Cinzel", serif;
    font-weight: 700;
    color: var(--sky);
    font-size: 42px;
    line-height: 49px;
    letter-spacing: 0.5px;
  }
  .contact-panel {
    position: absolute;
    left: 508px; top: 474px;
    width: 692px;
    height: 254px;
    background: var(--sky);
    padding: 50px 0 0 48px;
  }
  .contact-list { list-style: none; }
  .contact-item {
    display: flex;
    align-items: center;
    gap: 15px;
    height: 57px;
    font-family: "Cormorant Garamond", serif;
    font-weight: 500;
    font-size: 38px;
    color: var(--paper);
  }
  .contact-icon {
    width: 36px;
    height: 36px;
    flex: none;
  }
</style>
</head>
<body>
  <div class="card">
    <section class="brand-area">
      <div class="brand">
        <span class="brand-dot"></span>
        <h1 class="brand-name">
          <span class="primary">Brambleford</span>
          <span class="secondary">Landscape Construction</span>
        </h1>
      </div>
    </section>

    <section class="company-panel">
      <h2 class="company-name">Brambleford<br>Landscape<br>Construction</h2>
    </section>

    <section class="contact-panel">
      <ul class="contact-list">
        <li class="contact-item">
          <svg class="contact-icon" viewBox="0 0 36 36" aria-hidden="true">
            <circle cx="18" cy="18" r="18" fill="var(--leaf)"/>
            <path d="M12.5 10.5c1-.8 2-.6 2.6.3l1.6 2.5c.5.8.3 1.7-.4 2.3l-1 .8c.9 2 2.4 3.6 4.4 4.6l.8-1c.6-.7 1.5-.9 2.3-.4l2.5 1.6c.9.6 1.1 1.7.3 2.6l-1 1.1c-1 1-2.6 1.3-4 .7-4.3-1.9-7.5-5.2-9.3-9.5-.6-1.4-.3-3 .7-4z" fill="none" stroke="#ffffff" stroke-width="1.6" stroke-linejoin="round"/>
          </svg>
          <span>(877) 62Vista</span>
        </li>
        <li class="contact-item">
          <svg class="contact-icon" viewBox="0 0 36 36" aria-hidden="true">
            <circle cx="18" cy="18" r="18" fill="var(--leaf)"/>
            <g fill="none" stroke="#ffffff" stroke-width="1.6">
              <circle cx="18" cy="18" r="9"/>
              <ellipse cx="18" cy="18" rx="4" ry="9"/>
              <line x1="9" y1="18" x2="27" y2="18"/>
              <line x1="10.5" y1="13.5" x2="25.5" y2="13.5"/>
              <line x1="10.5" y1="22.5" x2="25.5" y2="22.5"/>
            </g>
          </svg>
          <span>Bramblefordyards.example</span>
        </li>
        <li class="contact-item">
          <svg class="contact-icon" viewBox="0 0 36 36" aria-hidden="true">
            <circle cx="18" cy="18" r="18" fill="var(--leaf)"/>
            <g fill="none" stroke="#ffffff" stroke-width="1.6" stroke-linejoin="round">
              <rect x="9.5" y="12" width="17" height="12" rx="1"/>
              <path d="M9.5 12.5 18 19l8.5-6.5"/>
              <path d="M9.5 23.5l6-5.5M26.5 23.5l-6-5.5"/>
            </g>
          </svg>
          <span>sales@bramblefordyards.example</span>
        </li>
      </ul>
    </section>
  </div>
</body>
</html>
```